Values and Organizational Purpose Signage

We recently solidified our company values, organizatioanal purpose and strategic vision. I'd like to develop some tasteful (not overly corporate) signage of these values to display in our office.

I've attached the hand-written values and purpose that my core team members then initialed acknowleding they align along with the signage at the front of our office to provide some perspective on our brand identity.

Industry/Entity Type

It Company

Font styles to use
Sans Serif

Requirements
Must have
• I'd like to see the values and org purpose depicted as one sign and as separate signs (i.e., values on one sign and org purpose on another). I need it to reflect our brand identity which I've uploaded

```html
<!DOCTYPE html>
<html lang="en">
<head>
<meta charset="utf-8">
<title>Organizational Purpose and Core Values</title>
<link href="https://fonts.googleapis.com/css2?family=Caladea&display=swap" rel="stylesheet">
<style>
  :root {
    --frame: #4a4f57;
    --paper: #ffffff;
    --accent: #bccf33;
    --ink: #4a4f57;
    --rule: #6e7074;
  }
  * { margin: 0; padding: 0; box-sizing: border-box; }
  html, body { width: 1200px; height: 917px; overflow: hidden; background: var(--frame); }
  body { font-family: "Caladea", Cambria, Georgia, serif; color: var(--ink); }
  .sign {
    position: absolute; left: 31px; top: 30px; width: 1138px; height: 855px;
    background: var(--paper);
  }
  .heading {
    position: absolute; color: var(--accent); font-weight: 400;
    font-size: 54px; line-height: 63px; white-space: nowrap;
  }
  .rule { position: absolute; height: 2.5px; background: var(--rule); }
  .purpose-text {
    position: absolute; left: 48px; top: 244px; width: 380px;
    font-size: 34px; line-height: 42px;
  }
  .value-name {
    position: absolute; left: 609px; color: var(--accent);
    font-size: 50px; line-height: 50px; font-weight: 400; white-space: nowrap;
  }
  .value-text {
    position: absolute; left: 611px; width: 448px;
    font-size: 25.5px; line-height: 31px;
  }
  .brand {
    position: absolute; left: 0; right: 0; top: 793px; text-align: center;
    font-size: 22px; line-height: 30px; color: var(--ink); letter-spacing: 1px;
  }
</style>
</head>
<body>
  <main class="sign">
    <h1 class="heading" style="left:48px; top:54px;">Organizational<br>Purpose</h1>
    <div class="rule" style="left:48px; top:202px; width:261px;"></div>
    <p class="purpose-text">We deliver simple and digestible solutions to complex matters.</p>

    <h2 class="heading" style="left:609px; top:54px;">Core Values<br>Defines</h2>
    <div class="rule" style="left:605px; top:202px; width:262px;"></div>

    <h3 class="value-name" style="top:233px;">Respect</h3>
    <p class="value-text" style="top:283px;">We are transparent and receptive to the thoughts, opinions, and feelings to others</p>

    <h3 class="value-name" style="top:378px;">Integrity</h3>
    <p class="value-text" style="top:436px;">We uphold our promises</p>

    <h3 class="value-name" style="top:490px;">Excellence</h3>
    <p class="value-text" style="top:546px;">We continuously strive to be the best in all endeavors</p>

    <h3 class="value-name" style="top:621px;">Open mindedness</h3>
    <p class="value-text" style="top:672px;">We encourage creative and innovative expressions</p>

    <div class="brand">Quellvantor</div>
  </main>
</body>
</html>
```